Business Card Design Project

We are looking for a new business card design to go with our new logo. We need to have a front and back card with our name and numberous phone numbers on the front and our addresses on the back. We will need to be able to edit the cards to have different names and numbers. Right now our card looks too busy and cluttered. We need to have our Brightmoor Estates Group Logo Prominently displayed. We will also need the Halvern Dunstead Portland Central, the relator logo and the equal housing logo on the front somewhere. We would like to have our addresses on the back along with the quote "Our most important goal is to exceed the expectations of our clients and the finest compliment we can received is a referral from a friend or past client. Thank you for your support!" Also, we would like the "Please follow us on : facebook logo, twitter loto, youtube logo and wordpress logo" I've attached our new logo and what our current business card looks like.

```html
<!DOCTYPE html>
<html lang="en">
<head>
<meta charset="utf-8">
<title>Brightmoor Estates Group – Business Cards</title>
<link href="https://fonts.googleapis.com/css2?family=Sorts+Mill+Goudy:ital@0;1&display=swap" rel="stylesheet">
<style>
  :root {
    --brand-red: #b9303a;
    --brand-red-dark: #9e2630;
    --ink: #1f1f1f;
    --muted: #8a8a8a;
    --paper: #ffffff;
    --backdrop: #ece9e4;
    --on-red: #f3e4e4;
  }
  * { box-sizing: border-box; margin: 0; padding: 0; }
  html, body { width: 1200px; height: 1000px; overflow: hidden; }
  body {
    background: var(--backdrop);
    font-family: "Sorts Mill Goudy", Georgia, serif;
    color: var(--ink);
    position: relative;
  }
  .card {
    position: absolute;
    top: 185px;
    width: 360px;
    height: 630px;
    background: var(--paper);
    box-shadow: 0 6px 18px rgba(0,0,0,0.18);
    overflow: hidden;
  }
  .card--back { left: 200px; }
  .card--front { left: 640px; }

  .wordmark {
    display: flex;
    align-items: center;
    justify-content: center;
    gap: 12px;
    color: var(--brand-red-dark);
    font-size: 30px;
    line-height: 1.05;
    text-align: left;
  }
  .wordmark__dot {
    width: 18px; height: 18px;
    border-radius: 50%;
    background: var(--brand-red-dark);
    flex: none;
  }

  /* Back card */
  .back__head {
    height: 160px;
    display: flex;
    align-items: center;
    justify-content: center;
  }
  .back__body {
    height: 470px;
    background: var(--brand-red);
    color: var(--on-red);
    text-align: center;
    padding: 22px 30px 0;
  }
  .quote {
    font-style: italic;
    font-size: 13.5px;
    line-height: 1.25;
    margin-bottom: 26px;
  }
  .office { margin-bottom: 14px; font-size: 14px; line-height: 1.2; }
  .office__name { font-size: 13px; opacity: 0.85; }
  .office__addr { font-weight: bold; }
  .follow { font-size: 14px; margin-top: 18px; }
  .social {
    display: flex;
    justify-content: center;
    gap: 16px;
    margin-top: 12px;
  }
  .social__icon {
    width: 36px; height: 36px;
    border-radius: 6px;
    background: var(--paper);
    opacity: 0.9;
  }

  /* Front card */
  .front__logo {
    position: absolute;
    top: 120px; left: 0; right: 0;
  }
  .agent {
    position: absolute;
    top: 290px; left: 40px; right: 30px;
  }
  .agent__name { color: var(--brand-red); font-size: 24px; font-weight: bold; }
  .agent__title { color: var(--muted); font-size: 15px; margin-top: 2px; }
  .contact {
    list-style: none;
    margin-top: 22px;
    font-size: 16px;
    line-height: 1.15;
  }
  .contact__label { color: var(--brand-red); }
  .links { margin-top: 16px; font-size: 15.5px; font-weight: bold; line-height: 1.25; }
  .affiliations {
    position: absolute;
    top: 525px; left: 30px; right: 30px;
    display: flex;
    align-items: center;
    justify-content: space-between;
  }
  .brokerage {
    display: flex; align-items: center; gap: 6px;
    color: var(--brand-red-dark);
    font-size: 11px;
    line-height: 1.05;
  }
  .brokerage__mark { width: 10px; height: 10px; background: var(--brand-red-dark); flex: none; }
  .badges { display: flex; gap: 18px; }
  .badge { width: 26px; height: 26px; background: var(--ink); }
  .front__band {
    position: absolute;
    bottom: 0; left: 0; right: 0;
    height: 52px;
    background: var(--brand-red);
  }
</style>
</head>
<body>

  <section class="card card--back" aria-label="Card back">
    <header class="back__head">
      <div class="wordmark"><span class="wordmark__dot"></span><span>Brightmoor<br>Estates Group</span></div>
    </header>
    <div class="back__body">
      <p class="quote">“Our most important goal is to exceed the expections of our clients and the finest compliment we can recieve is a referral from a friend or past client. Thank you for your support!”</p>
      <div class="office">
        <div class="office__name">Alder Crest Office</div>
        <div class="office__addr">4120 SE Alder Crest Rd, #210<br>Portland, OR 97206</div>
      </div>
      <div class="office">
        <div class="office__name">Juniper Office</div>
        <div class="office__addr">815 NE Juniper St<br>Ste 740<br>Portland, OR 97211</div>
      </div>
      <div class="office">
        <div class="office__name">Boise Office</div>
        <div class="office__addr">2240 S Ridgeview Pl<br>Boise<br>ID 83705</div>
      </div>
      <p class="follow">Please follow us on:</p>
      <div class="social">
        <span class="social__icon" role="img" aria-label="Social network link"></span>
        <span class="social__icon" role="img" aria-label="Social network link"></span>
        <span class="social__icon" role="img" aria-label="Video channel link"></span>
        <span class="social__icon" role="img" aria-label="Blog link"></span>
      </div>
    </div>
  </section>

  <section class="card card--front" aria-label="Card front">
    <div class="front__logo">
      <div class="wordmark"><span class="wordmark__dot"></span><span>Brightmoor<br>Estates Group</span></div>
    </div>
    <div class="agent">
      <div class="agent__name">Clara Whitford</div>
      <div class="agent__title">Broker, Listings Specialist</div>
      <ul class="contact">
        <li>(503) 555-0147 <span class="contact__label">cell</span></li>
        <li>(503) 555-0182 <span class="contact__label">office</span></li>
        <li>(800) 555-0163 <span class="contact__label">toll free</span></li>
        <li>(503) 555-0119 <span class="contact__label">fax</span></li>
      </ul>
      <div class="links">
        <div>clara@brightmoorestates.com</div>
        <div>www.brightmoorestates.com</div>
      </div>
    </div>
    <div class="affiliations">
      <div class="brokerage"><span class="brokerage__mark"></span><span>Halvern Dunstead<br>Portland Central</span></div>
      <div class="badges">
        <span class="badge" role="img" aria-label="Realtor membership badge"></span>
        <span class="badge" role="img" aria-label="Equal housing badge"></span>
      </div>
    </div>
    <div class="front__band"></div>
  </section>

</body>
</html>
```